Artsy 1 Page Website/Brochure for climate change investment company

We want art like feel similar to https://velmora.quintrel.net/ for a 1 page online website (1 page) to have an online presence. We want to show credibility, no functionality. The only call to action is an email to the company.
3 sections 1) Company 2) Services, 3) brands.
The idea is 1) we are credible and serious, 2) market is increasing, 3) knowledge about sector, 4) large branded companies in the sector.
We want users to be interested and want to learn more.
There should be 1 or 2 animated sections. 1) GHG (green house gases) floating up or something showing emissions rising, 2) Services can scroll or loop.
See my mockup. The font should be standardized. The text shapes should be same. Keep same color palette unless you have better idea.
https://slides.brovanta.com/deck/7KxQ2mPzT9wLbV4nRfYcHd8sJuA6eGtNqXoZ1iMvBkE/view?ref=share
Logo for company AirLedgerHub.com

Target Market(s)

Potential Investors and Academics and Industry specialist. This is not for general consumers

Industry/Entity Type

Environment/Investors

Number of Pages Required

1 page

Requirements
Must have
• Artsy feel like a brochure
Should not have
• I do not want a functional website with lots of standard menus e.g. menus at the top

```html
<!DOCTYPE html>
<html lang="en">
<head>
<meta charset="utf-8">
<title>AirLedger Hub</title>
<link href="https://fonts.googleapis.com/css2?family=Montserrat:wght@500;600;700&display=swap" rel="stylesheet">
<style>
  :root {
    --magenta: #c4004f;
    --wine: #7a0a2c;
    --taupe: #7a7365;
    --charcoal: #232323;
    --white: #ffffff;
    --logo-grey: #9a9a9a;
    --rule-grey: #6a6a6a;
    --list-ink: #1d1d1d;
    --font: "Montserrat", Arial, sans-serif;
  }
  * { margin: 0; padding: 0; box-sizing: border-box; }
  html, body { width: 1200px; height: 2376px; overflow: hidden; background: var(--white); font-family: var(--font); }
  .page { position: relative; width: 1200px; height: 2376px; }

  .panel { position: absolute; left: 32px; width: 1138px; height: 731px; overflow: hidden; color: var(--white); }
  .panel--company { top: 26px; background: var(--magenta); }
  .panel--services { top: 790px; background: var(--taupe); }
  .panel--space { top: 1553px; background: var(--charcoal); }

  .backdrop { position: absolute; inset: 0; }
  .panel--company .backdrop { background: radial-gradient(ellipse 60% 50% at 55% 75%, rgba(255,40,120,.75), transparent 70%), linear-gradient(160deg, var(--magenta) 20%, #e0105e 60%, #d60a58 100%); }
  .panel--services .backdrop { background: radial-gradient(ellipse 45% 55% at 50% 65%, rgba(170,165,150,.7), transparent 70%), linear-gradient(180deg, #767062 0%, #857e6f 60%, #7a7365 100%); }
  .panel--space .backdrop { background: radial-gradient(ellipse 55% 35% at 55% 95%, rgba(90,60,40,.35), transparent 70%), var(--charcoal); }

  .gas-tabs { position: absolute; left: 42px; top: 67px; width: 37px; }
  .gas-tab { position: absolute; left: 0; width: 37px; height: 100px; border: 1.5px solid var(--wine); border-radius: 3px;
    display: flex; align-items: center; justify-content: center; }
  .gas-tab span { writing-mode: vertical-rl; transform: rotate(180deg); font-size: 15px; font-weight: 600; color: var(--wine); letter-spacing: .5px; }
  .gas-tab sub { font-size: 8px; }
  .gas-tab:nth-child(1) { top: 0; }
  .gas-tab:nth-child(2) { top: 110px; }
  .gas-tab:nth-child(3) { top: 226px; }
  .panel--space .gas-tab { border-color: #5a1424; }
  .panel--space .gas-tab span { color: #5a1424; }

  .side-brand { position: absolute; left: 44px; bottom: 66px; writing-mode: vertical-rl; transform: rotate(180deg);
    font-size: 33px; font-weight: 700; color: var(--white); white-space: nowrap; }

  .brand-title { position: absolute; left: 0; right: 0; top: 48px; text-align: center; font-size: 72px; font-weight: 700; letter-spacing: .5px; }
  .hero-word { position: absolute; left: 0; right: 0; top: 246px; text-align: center; font-size: 138px; font-weight: 700; line-height: 1; letter-spacing: 2px; }
  .section-title { position: absolute; left: 0; right: 0; top: 52px; text-align: center; font-size: 66px; font-weight: 700; line-height: 1; }

  .connect { position: absolute; left: 843px; top: 591px; width: 171px; height: 41px; background: var(--wine);
    border: 1px solid rgba(255,255,255,.85); border-radius: 2px; display: flex; align-items: center; justify-content: center;
    font-size: 16px; font-weight: 600; letter-spacing: 3.5px; color: var(--white); }
  .connect::after { content: ""; position: absolute; left: 104px; bottom: -11px; border-left: 9px solid transparent; border-top: 11px solid var(--wine); }
  .email { position: absolute; left: 842px; top: 660px; font-size: 17px; font-weight: 600; color: var(--white); }

  .service-tag { position: absolute; background: var(--magenta); color: var(--white); font-size: 18px; font-weight: 600; letter-spacing: 4px;
    display: flex; align-items: center; justify-content: center; }
  .service-tag--capture { left: 425px; top: 155px; width: 287px; height: 49px; }
  .service-tag--nature { left: 368px; top: 211px; width: 402px; height: 49px; }
  .service-list { position: absolute; left: 376px; top: 267px; width: 385px; height: 367px; border: 2px solid rgba(255,255,255,.9);
    background: linear-gradient(180deg, rgba(255,255,255,.02), rgba(255,255,255,.14)); list-style: none; padding: 22px 0 0 42px; }
  .service-list li { font-size: 18px; font-weight: 500; color: var(--list-ink); height: 42px; display: flex; align-items: center; }
  .service-list li svg { margin-right: 7px; }

  .partner-row { position: absolute; left: 0; right: 0; height: 30px; display: flex; align-items: center; justify-content: center; }
  .partner-row--one { top: 208px; }
  .partner-row--two { top: 296px; }
  .partner-row--three { top: 402px; }
  .partner { font-size: 22px; font-weight: 700; color: var(--logo-grey); display: flex; align-items: center; white-space: nowrap; padding: 0 16px; line-height: 30px; }
  .partner + .partner { border-left: 2px solid var(--rule-grey); }
  .partner .mark { width: 20px; height: 20px; background: var(--logo-grey); margin-right: 10px; }
  .partner .mark--round { border-radius: 50%; }
  .row-rule { position: absolute; left: 199px; width: 740px; height: 1.5px; background: var(--rule-grey); }
  .row-rule--one { top: 267px; }
  .row-rule--two { top: 369px; }
</style>
</head>
<body>
<main class="page">

  <section class="panel panel--company">
    <div class="backdrop" role="img" aria-label="Flowing pink wave-line artwork with a faint globe rising at centre"></div>
    <div class="gas-tabs">
      <div class="gas-tab"><span>CH<sub>4</sub> ↗</span></div>
      <div class="gas-tab"><span>GHG ↗</span></div>
      <div class="gas-tab"><span>CO<sub>2</sub> ↗</span></div>
    </div>
    <h1 class="brand-title">AirLedger Hub</h1>
    <div class="hero-word">GHGs</div>
    <div class="connect">CONNECT</div>
    <div class="email">Partners@AirLedgerHub.com</div>
  </section>

  <section class="panel panel--services">
    <div class="backdrop" role="img" aria-label="Soft taupe wave-line artwork"></div>
    <div class="gas-tabs">
      <div class="gas-tab"><span>CH<sub>4</sub> ↗</span></div>
      <div class="gas-tab"><span>GHG ↗</span></div>
      <div class="gas-tab"><span>CO<sub>2</sub> ↗</span></div>
    </div>
    <div class="side-brand">AirLedger Hub</div>
    <h2 class="section-title">Services</h2>
    <div class="service-tag service-tag--capture">CARBON CAPTURE</div>
    <div class="service-tag service-tag--nature">NATURE BASED SOLUTIONS</div>
    <ul class="service-list">
      <li><svg width="16" height="8" viewBox="0 0 16 8"><path d="M0 4h13M10 1l4 3-4 3" stroke="#c4004f" stroke-width="2" fill="none"/></svg>Technology based solutions</li>
      <li><svg width="16" height="8" viewBox="0 0 16 8"><path d="M0 4h13M10 1l4 3-4 3" stroke="#c4004f" stroke-width="2" fill="none"/></svg>Permanent Carbon Removal</li>
      <li><svg width="16" height="8" viewBox="0 0 16 8"><path d="M0 4h13M10 1l4 3-4 3" stroke="#c4004f" stroke-width="2" fill="none"/></svg>New Methodologies</li>
      <li><svg width="16" height="8" viewBox="0 0 16 8"><path d="M0 4h13M10 1l4 3-4 3" stroke="#c4004f" stroke-width="2" fill="none"/></svg>REDD+</li>
      <li><svg width="16" height="8" viewBox="0 0 16 8"><path d="M0 4h13M10 1l4 3-4 3" stroke="#c4004f" stroke-width="2" fill="none"/></svg>Streaming</li>
      <li><svg width="16" height="8" viewBox="0 0 16 8"><path d="M0 4h13M10 1l4 3-4 3" stroke="#c4004f" stroke-width="2" fill="none"/></svg>Carbon Markets</li>
    </ul>
    <div class="connect">CONNECT</div>
    <div class="email">Partners@AirLedgerHub.com</div>
  </section>

  <section class="panel panel--space">
    <div class="backdrop" role="img" aria-label="Dark backdrop with faint rippling globe artwork"></div>
    <div class="gas-tabs">
      <div class="gas-tab"><span>CH<sub>4</sub> ↗</span></div>
      <div class="gas-tab"><span>GHG ↗</span></div>
      <div class="gas-tab"><span>CO<sub>2</sub> ↗</span></div>
    </div>
    <div class="side-brand">AirLedger Hub</div>
    <h2 class="section-title">Our Space</h2>

    <div class="partner-row partner-row--one">
      <div class="partner">Soltervine</div>
      <div class="partner">Drenvolt</div>
      <div class="partner"><span class="mark mark--round"></span>Hollin Carbon Accord</div>
      <div class="partner">Mercivo</div>
    </div>
    <div class="row-rule row-rule--one"></div>
    <div class="partner-row partner-row--two">
      <div class="partner">Tenderqo</div>
      <div class="partner">Quorisk</div>
      <div class="partner"><span class="mark"></span>Halvren Union Council</div>
      <div class="partner">Brannoch Institute</div>
    </div>
    <div class="row-rule row-rule--two"></div>
    <div class="partner-row partner-row--three">
      <div class="partner">Orvelle Mark</div>
      <div class="partner">Dunmere Grid Inc.</div>
      <div class="partner"><span class="mark"></span>Trelwyn Panel</div>
      <div class="partner">Ashvale Summit</div>
    </div>

    <div class="connect">CONNECT</div>
    <div class="email">Partners@AirLedgerHub.com</div>
  </section>

</main>
</body>
</html>
```